physical therapy flyer

2 office locations speciality programs - work injury / Motor vehicle accidents - spanish speaking - do not put balance defecits/ fall prevention - Spanish speaking
neck and back pain shoulder pain/ rotator cuff disorder / bursitis
hip pain knee andle and foot pain post operative care including Spine , shoulder , knee , total joint replacement

Meadowlark Physical therapy & Chiropractic
4871 Pinecrest BLvd
dalton heights ny 10592
7185820147
3715 Tillman Parkway
Fernvale NY 10592
7189043218
www.meadowlarkptrehab.com

```html
<!DOCTYPE html>
<html lang="en">
<head>
<meta charset="utf-8">
<title>Meadowlark Physical Therapy &amp; Chiropractic Flyer</title>
<link href="https://fonts.googleapis.com/css2?family=Poppins:wght@400;500;600;700;800&family=Oswald:wght@500;600;700&family=Open+Sans:wght@400;500&display=swap" rel="stylesheet">
<style>
  :root{
    --paper:#e4e4e4;
    --paper-light:#f2f2f2;
    --ink:#2b1914;
    --text:#1e1e1e;
    --green:#5aa81a;
    --green-deep:#23874a;
    --green-dark:#1e6e3e;
    --lime:#74d60f;
    --row:#c7e48a;
    --badge:#072626;
    --tab:#222;
  }
  *{margin:0;padding:0;box-sizing:border-box}
  html,body{width:935px;height:1200px;overflow:hidden}
  body{background:var(--paper);font-family:"Poppins",sans-serif;color:var(--text)}
  .flyer{position:relative;width:935px;height:1200px;overflow:hidden;
    background:radial-gradient(ellipse at 30% 45%,var(--paper-light) 0%,var(--paper) 60%,#d9d9d9 100%)}
  .hero-photo{position:absolute;left:430px;top:0;width:505px;height:1200px;
    background:
      radial-gradient(ellipse 120px 200px at 430px 260px,rgba(232,82,38,.85),rgba(232,82,38,0) 100%),
      radial-gradient(ellipse 180px 420px at 420px 620px,rgba(210,110,110,.55),rgba(210,110,110,0) 100%),
      linear-gradient(100deg,rgba(228,228,228,1) 0%,rgba(228,228,228,0) 35%),
      linear-gradient(180deg,#6b6f77 0%,#b8bcc2 22%,#dcdcdc 55%,#e6e6e6 100%)}
  .brand{position:absolute;left:48px;top:72px;display:flex;align-items:center;gap:12px}
  .brand-dot{width:44px;height:44px;border-radius:50%;background:var(--ink)}
  .brand-name{font-family:"Open Sans",sans-serif;font-size:17px;line-height:20px;color:var(--ink)}
  .title-top{position:absolute;left:48px;top:176px;font-size:44px;font-weight:800;letter-spacing:9px;color:var(--green)}
  .title-main{position:absolute;left:46px;top:226px;font-size:51px;font-weight:800;letter-spacing:-1px;color:var(--ink);line-height:56px}
  .title-sub{position:absolute;left:46px;top:280px;font-size:51px;font-weight:400;color:var(--ink);line-height:56px}
  .tagline{position:absolute;left:48px;top:364px;height:62px;border-left:8px solid var(--green);padding-left:22px;font-size:24px;font-weight:500;line-height:31px;color:#222}
  .section-title{position:absolute;left:48px;top:456px;font-size:31px;font-weight:700;color:var(--green-deep)}
  .treatments{position:absolute;left:48px;top:520px;list-style:none}
  .treatment{position:relative;height:51px;width:530px;margin-bottom:16px;display:flex;align-items:center;
    background:linear-gradient(90deg,var(--row) 0%,var(--row) 55%,rgba(199,228,138,0) 100%)}
  .treatment:nth-child(2){margin-bottom:14px}
  .treatment .icon{position:absolute;left:-2px;top:-4px;width:59px;height:59px;border-radius:50%;background:#4f9a45;display:flex;align-items:center;justify-content:center}
  .treatment .label{margin-left:72px;font-size:19px;font-weight:500;color:#1b1b1b}
  .rehab-title{position:absolute;left:50px;top:862px;font-size:18px;font-weight:700;letter-spacing:4.3px;color:#1e1e1e}
  .pills{position:absolute;left:44px;top:902px;display:flex;gap:6px;list-style:none}
  .pill{height:36px;border:1.5px solid var(--green);border-radius:18px;display:flex;align-items:center;padding:0 10px 0 10px;font-size:16px;color:#222;gap:10px;white-space:nowrap}
  .pill svg{flex:none}
  .pill.spine{width:112px}
  .pill.shoulder{width:120px}
  .pill.knee{width:108px}
  .pill.joints{width:272px}
  .locations-heading{position:absolute;left:58px;top:982px;text-align:center;line-height:1}
  .locations-heading .big{display:block;font-size:56px;font-weight:800;color:var(--green-deep);letter-spacing:-1px}
  .locations-heading .small{display:block;font-family:"Oswald",sans-serif;font-size:30px;font-weight:600;color:#2a2a2a;margin-top:2px;transform:scaleX(.85);transform-origin:left}
  .location{position:absolute;top:960px;width:272px;height:126px;border-radius:0 0 24px 0;overflow:hidden}
  .location.primary{left:231px;background:var(--green)}
  .location.secondary{left:517px;background:var(--green-deep)}
  .location .tab{position:absolute;right:0;top:0;height:26px;background:var(--tab);
    clip-path:polygon(0 0,100% 0,100% 100%,26px 100%);display:flex;align-items:center;
    padding:0 20px 0 34px;white-space:nowrap;
    font-size:15px;font-weight:700;color:#fff}
  .location .address{position:absolute;left:12px;top:36px;right:10px;display:flex;gap:8px;font-size:13.2px;font-weight:700;color:#fff;line-height:17px}
  .location .phone{position:absolute;left:0;right:0;bottom:0;height:44px;display:flex;align-items:center;gap:8px;padding-left:12px;
    font-size:26px;font-weight:700;color:#fff;background:rgba(0,0,0,.06);border-top:1px solid rgba(255,255,255,.12)}
  .web-bar{position:absolute;left:55px;top:1114px;width:727px;height:37px;border-radius:19px;background:var(--green-dark);overflow:hidden}
  .web-bar .lead{position:absolute;left:0;top:0;width:221px;height:37px;display:flex;align-items:center;justify-content:center;font-size:17px;font-weight:500;letter-spacing:3.5px;color:var(--row)}
  .web-bar .url{position:absolute;left:216px;top:0;right:0;height:37px;border-radius:19px;background:var(--green);display:flex;align-items:center;justify-content:center;
    font-size:18px;font-weight:700;letter-spacing:5.2px;color:#fff}
  .badge{position:absolute;left:540px;top:596px;width:262px;height:262px}
  .badge-text{position:absolute;left:0;top:0;width:262px;height:262px;display:flex;flex-direction:column;align-items:center;justify-content:center;
    font-family:"Oswald",sans-serif;transform:rotate(-8deg);line-height:.95}
  .badge-text .kicker{font-size:19px;font-weight:600;color:#fff}
  .badge-text .headline{font-size:38px;font-weight:700;color:var(--lime)}
</style>
</head>
<body>
<main class="flyer">
  <div class="hero-photo" role="img" aria-label="Photo of a man holding his sore neck and shoulder, with a highlighted spine illustration running down the right edge"></div>

  <header class="brand">
    <span class="brand-dot"></span>
    <span class="brand-name">Meadowlark Physical Therapy,<br>Chiropractic, and Acupuncture</span>
  </header>

  <h1>
    <span class="title-top">MEADOWLARK</span>
    <span class="title-main">PHYSICAL THERAPY</span>
    <span class="title-sub">&amp; CHIROPRACTIC</span>
  </h1>

  <p class="tagline">Comprehensive Care Across<br>Two Locations!</p>

  <h2 class="section-title">Specialized Treatment for:</h2>

  <ul class="treatments">
    <li class="treatment">
      <span class="icon"><svg width="34" height="34" viewBox="0 0 34 34" fill="none" stroke="#fff" stroke-width="1.6"><rect x="12" y="2" width="10" height="30" rx="5" transform="rotate(45 17 17)"/><rect x="12" y="2" width="10" height="30" rx="5" transform="rotate(-45 17 17)"/></svg></span>
      <span class="label">Work-Related Injuries</span>
    </li>
    <li class="treatment">
      <span class="icon"><svg width="38" height="30" viewBox="0 0 38 30" fill="none" stroke="#fff" stroke-width="1.6"><circle cx="8" cy="21" r="5"/><circle cx="24" cy="21" r="5"/><path d="M8 21l6-9h8l2 9M14 12l-3-4h5"/><rect x="31" y="4" width="4" height="22" rx="1"/></svg></span>
      <span class="label">Motor Vehicle Accident Recovery</span>
    </li>
    <li class="treatment">
      <span class="icon"><svg width="30" height="34" viewBox="0 0 30 34" fill="none" stroke="#fff" stroke-width="1.6"><path d="M10 3c-1 4-6 5-7 9 0 7 2 14 4 19h16c2-5 4-12 4-19-1-4-6-5-7-9"/><path d="M15 8v20"/><circle cx="15" cy="18" r="5"/></svg></span>
      <span class="label">Neck, Back, and Shoulder Pain</span>
    </li>
    <li class="treatment">
      <span class="icon"><svg width="30" height="34" viewBox="0 0 30 34" fill="none" stroke="#fff" stroke-width="1.6"><path d="M12 2v18c0 4-8 5-8 9v2h22v-3c0-3-4-4-4-8V2"/><circle cx="17" cy="22" r="3"/></svg></span>
      <span class="label">Hip, Knee, Ankle, and Foot Pain</span>
    </li>
    <li class="treatment">
      <span class="icon"><svg width="36" height="30" viewBox="0 0 36 30" fill="none" stroke="#fff" stroke-width="1.6"><circle cx="11" cy="18" r="9"/><circle cx="25" cy="11" r="9"/><path d="M8 22l3-8 3 8M9 20h4M21 9h8M25 7v2M22 15l5-6"/></svg></span>
      <span class="label">Bilingual Services – Spanish Available</span>
    </li>
  </ul>

  <div class="badge">
    <svg width="262" height="262" viewBox="0 0 262 262" aria-hidden="true">
      <path fill="var(--badge)" d="M131 6 L149 26 L173 14 L184 39 L211 36 L212 63 L238 70 L230 95 L252 112 L236 133 L252 154 L230 170 L238 195 L212 202 L211 229 L184 226 L173 251 L149 239 L131 258 L113 239 L89 251 L78 226 L51 229 L50 202 L24 195 L32 170 L10 154 L26 133 L10 112 L32 95 L24 70 L50 63 L51 36 L78 39 L89 14 L113 26 Z" stroke="var(--badge)" stroke-width="10" stroke-linejoin="round"/>
    </svg>
    <div class="badge-text">
      <span class="kicker">SPANISH-SPEAKING</span>
      <span class="headline">SERVICES</span>
      <span class="headline">AVAILABLE</span>
    </div>
  </div>

  <h3 class="rehab-title">POST-SURGICAL REHABILITATION</h3>
  <ul class="pills">
    <li class="pill spine"><svg width="14" height="14" viewBox="0 0 14 14"><circle cx="7" cy="7" r="7" fill="var(--green)"/><path d="M4 7l2 2 4-4" stroke="#fff" stroke-width="1.8" fill="none"/></svg>Spine</li>
    <li class="pill shoulder"><svg width="14" height="14" viewBox="0 0 14 14"><circle cx="7" cy="7" r="7" fill="var(--green)"/><path d="M4 7l2 2 4-4" stroke="#fff" stroke-width="1.8" fill="none"/></svg>Shoulder</li>
    <li class="pill knee"><svg width="14" height="14" viewBox="0 0 14 14"><circle cx="7" cy="7" r="7" fill="var(--green)"/><path d="M4 7l2 2 4-4" stroke="#fff" stroke-width="1.8" fill="none"/></svg>Knee</li>
    <li class="pill joints"><svg width="14" height="14" viewBox="0 0 14 14"><circle cx="7" cy="7" r="7" fill="var(--green)"/><path d="M4 7l2 2 4-4" stroke="#fff" stroke-width="1.8" fill="none"/></svg>Total Joint Replacements</li>
  </ul>

  <h2 class="locations-heading"><span class="big">OUR</span><span class="small">LOCATIONS</span></h2>

  <section class="location primary">
    <div class="tab">DALTON HEIGHTS</div>
    <p class="address"><svg width="14" height="16" viewBox="0 0 14 16" style="flex:none;margin-top:2px"><circle cx="7" cy="8" r="7" fill="#222"/><circle cx="7" cy="7" r="2.4" fill="none" stroke="#fff" stroke-width="1.4"/></svg>Dalton Heights: 4871 Pinecrest Blvd, NY 10592</p>
    <p class="phone"><svg width="14" height="14" viewBox="0 0 14 14"><circle cx="7" cy="7" r="7" fill="#222"/><path d="M5 4l1.5 2-1 1c.6 1.1 1.4 1.9 2.5 2.5l1-1 2 1.5-1 1.5C7 11 3.5 7.5 4 5z" fill="#fff"/></svg>718-582-0147</p>
  </section>

  <section class="location secondary">
    <div class="tab">FERNVALE</div>
    <p class="address"><svg width="14" height="16" viewBox="0 0 14 16" style="flex:none;margin-top:2px"><circle cx="7" cy="8" r="7" fill="#222"/><circle cx="7" cy="7" r="2.4" fill="none" stroke="#fff" stroke-width="1.4"/></svg>3715 Tillman Parkway,<br>NY 10592</p>
    <p class="phone"><svg width="14" height="14" viewBox="0 0 14 14"><circle cx="7" cy="7" r="7" fill="#222"/><path d="M5 4l1.5 2-1 1c.6 1.1 1.4 1.9 2.5 2.5l1-1 2 1.5-1 1.5C7 11 3.5 7.5 4 5z" fill="#fff"/></svg>718-904-3218</p>
  </section>

  <footer class="web-bar">
    <span class="lead">VISIT US AT</span>
    <span class="url">www.meadowlarkptrehab.com</span>
  </footer>
</main>
</body>
</html>
```